Vantro cards

I am in the auto motive, transportation business I would like a business card that is Something cool, modern edgy, having to do with car culture. I offer towing service for high and exotic cars. I also provide towing for collisions and car accidents. I offer open and enclosed transport nationwide.

Target Market(s)

Car culture people high end auto collectors

Industry/Entity Type

Towing car carrier

Contact Information for Business Card

My company colors black yellow and silver

Font styles to use
Serif

```html
<!DOCTYPE html>
<html lang="en">
<head>
<meta charset="utf-8">
<title>Vantro business cards</title>
<link href="https://fonts.googleapis.com/css2?family=Poppins:wght@400;500&family=Roboto+Slab:wght@700;800&display=swap" rel="stylesheet">
<style>
  :root {
    --stage: #0d0d0d;
    --yellow: #f9e05e;
    --black: #000000;
    --white: #ffffff;
    --ink: #111111;
  }
  * { margin: 0; padding: 0; box-sizing: border-box; }
  html, body { width: 1075px; height: 1200px; overflow: hidden; background: var(--stage); }
  .stage { position: relative; width: 1075px; height: 1200px; }

  .card { position: absolute; width: 663px; height: 394px; overflow: hidden; box-shadow: 3px 3px 6px rgba(0,0,0,.6); }
  .card--front { left: 206px; top: 187px; background: var(--white); }
  .card--back { left: 203px; top: 637px; background: var(--yellow); }

  .front-art { position: absolute; left: 0; top: 0; }

  .holder { position: absolute; left: 35px; top: 111px; color: var(--ink); }
  .holder__name { font-family: "Roboto Slab", Georgia, serif; font-weight: 800; font-size: 23px; line-height: 1; letter-spacing: .3px; white-space: nowrap; }
  .holder__role { font-family: "Poppins", Arial, sans-serif; font-size: 18.5px; line-height: 1.2; margin-top: 2px; white-space: nowrap; }

  .address { position: absolute; left: 37px; top: 184px; font-family: "Poppins", Arial, sans-serif; font-size: 18.5px; line-height: 23.5px; color: var(--ink); white-space: nowrap; }

  .contacts { position: absolute; left: 35px; top: 283px; list-style: none; font-family: "Poppins", Arial, sans-serif; font-size: 18.5px; line-height: 23.5px; color: var(--ink); white-space: nowrap; }
  .contacts li { display: flex; align-items: center; gap: 6px; }
  .contacts svg { width: 17px; height: 17px; flex: none; }

  .brand { position: absolute; display: flex; align-items: center; gap: 10px; font-family: "Roboto Slab", Georgia, serif; font-weight: 800; color: var(--black); letter-spacing: 1px; white-space: nowrap; }
  .brand__mark { background: var(--black); flex: none; }
  .brand--front { left: 467px; top: 165px; transform: translate(-50%, -50%); font-size: 46px; }
  .brand--front .brand__mark { width: 18px; height: 18px; }
  .brand--back { left: 50%; top: 50%; transform: translate(-50%, -50%); font-size: 60px; }
  .brand--back .brand__mark { width: 24px; height: 24px; }
</style>
</head>
<body>
<main class="stage">
  <section class="card card--front" aria-label="Business card front">
    <svg class="front-art" width="663" height="394" viewBox="0 0 663 394" aria-hidden="true">
      <rect x="0" y="0" width="467" height="97" fill="var(--yellow)"/>
      <rect x="467" y="0" width="196" height="97" fill="var(--black)"/>
      <path d="M336 97 L336 82 Q336 68 350 62 L467 18 L584 62 Q596 68 596 82 L596 97 Z" fill="var(--white)"/>
    </svg>

    <div class="holder">
      <h1 class="holder__name">MARCUS HALE</h1>
      <p class="holder__role">MANAGING DIRECTOR</p>
    </div>

    <p class="address">87, QUARRY BEND ROAD<br>NEWARK 07114<br>UNITED STATES</p>

    <ul class="contacts">
      <li>
        <svg viewBox="0 0 24 24"><path d="M6.6 10.8a15 15 0 0 0 6.6 6.6l2.2-2.2a1 1 0 0 1 1-.25 11.4 11.4 0 0 0 3.6.57 1 1 0 0 1 1 1V20a1 1 0 0 1-1 1A17 17 0 0 1 3 4a1 1 0 0 1 1-1h3.5a1 1 0 0 1 1 1c0 1.250.2 2.45.57 3.57a1 1 0 0 1-.25 1z" fill="var(--ink)"/></svg>
        044-555 218 730
      </li>
      <li>
        <svg viewBox="0 0 24 24"><rect x="2" y="5" width="20" height="14" fill="var(--ink)"/><path d="M2 5l10 8 10-8" fill="none" stroke="var(--white)" stroke-width="1.6"/></svg>
        HELLO@VANTROHAUL.COM
      </li>
      <li>
        <svg viewBox="0 0 24 24" fill="none" stroke="var(--ink)" stroke-width="1.8"><circle cx="12" cy="12" r="9.5"/><ellipse cx="12" cy="12" rx="4" ry="9.5"/><path d="M2.5 12h19M4 7h16M4 17h16"/></svg>
        WWW.VANTROHAUL.COM
      </li>
    </ul>

    <div class="brand brand--front"><span class="brand__mark"></span>VANTRO</div>
  </section>

  <section class="card card--back" aria-label="Business card back">
    <div class="brand brand--back"><span class="brand__mark"></span>VANTRO</div>
  </section>
</main>
</body>
</html>
```